Awesome Business Card Design needed!

Hey there.
I'm looking for a simple but awesome business card design.
Type of company: Online advertisement agency
(please don't use the typical business people or statistics images on the card)
The front has to display the business name
and possibly some sort of logo ( perhaps something with the two M's of the biz name )
And the back of the card should say:
Name
Phone
Email
Let your imagination flow.
here are some designs that I like and that you can use as inspiration.
Simple but Awesome
http://images.lumavexo.com/designs/55128_877673_43091_thumbnail.jpg
http://images.lumavexo.com/designs/37714_747642_40106_image.jpg
http://images.lumavexo.com/designs/55128_877673_43091_image.jpg
http://images.lumavexo.com/designs/51321_781878_43091_image.jpg
http://images.lumavexo.com/designs/33378_399063_15912_image.jpg
http://images.lumavexo.com/designs/2337_271604_9495_image.jpg
good luck

```html
<!DOCTYPE html>
<html lang="en">
<head>
<meta charset="utf-8">
<title>Corvane Media – Business Cards</title>
<link rel="stylesheet" href="https://fonts.googleapis.com/css2?family=Cinzel:wght@400&family=Crimson+Text:wght@400&family=Open+Sans:wght@400&display=swap">
<style>
  :root {
    --stage: #eeeae4;
    --card-black: #050505;
    --card-charcoal: #1b1b1d;
    --band-grey-top: #4a494b;
    --band-grey-bottom: #2a2a2c;
    --card-white: #ffffff;
    --teal: #2f8fa6;
    --teal-light: #4fb4c9;
    --blue-bar-top: #35a9dc;
    --blue-bar-bottom: #0a6fa3;
    --ink: #1a1a1a;
    --paper-text: #f2f2f2;
  }
  * { box-sizing: border-box; margin: 0; padding: 0; }
  html, body { width: 1200px; height: 900px; overflow: hidden; }
  body { background: var(--stage); position: relative; font-family: "Crimson Text", Georgia, serif; }

  .card {
    position: absolute;
    width: 560px;
    height: 320px;
    border-radius: 30px;
    overflow: hidden;
    box-shadow: 0 12px 30px rgba(0,0,0,.22);
  }
  .card--front { left: 60px; top: 110px; background: var(--card-black); }
  .card--back { left: 580px; top: 470px; background: var(--card-white); }

  .front-band {
    position: absolute; left: 0; right: 0; top: 56px; height: 208px;
    background: linear-gradient(180deg, var(--band-grey-top), var(--band-grey-bottom));
    border-top: 2px solid #5b5a5c;
    border-bottom: 2px solid #3a393b;
  }

  .brand {
    position: absolute; left: 0; right: 0; text-align: center;
  }
  .brand__name {
    display: inline-flex; align-items: center; gap: 12px;
    font-family: "Cinzel", "Times New Roman", serif;
    font-weight: 400; font-size: 36px; letter-spacing: 1px;
    color: var(--teal);
  }
  .brand__mark { width: 18px; height: 18px; background: var(--teal); }
  .brand__tagline {
    display: block; margin-top: 4px;
    font-size: 24px; letter-spacing: .3px;
  }
  .card--front .brand { top: 112px; }
  .card--front .brand__tagline { color: var(--paper-text); }
  .card--back .brand { top: 68px; }
  .card--back .brand__tagline { color: var(--ink); }

  .accent-bar {
    position: absolute; width: 130px; height: 22px;
    background: linear-gradient(90deg, var(--blue-bar-bottom), var(--blue-bar-top));
  }
  .card--front .accent-bar { left: 322px; top: 210px; }
  .card--back .accent-bar { right: 0; top: 176px; width: 150px; }

  .back-strip {
    position: absolute; left: 0; right: 0; bottom: 0; height: 122px;
    background: var(--card-charcoal);
  }
  .person {
    position: absolute; right: 30px; top: 16px; text-align: right;
  }
  .person__name { font-size: 30px; color: var(--teal); line-height: 1; }
  .person__role { font-size: 17px; color: var(--paper-text); margin-top: 4px; }

  .contacts {
    position: absolute; left: 26px; bottom: 18px; list-style: none;
    font-family: "Open Sans", Arial, sans-serif; font-size: 17px; color: var(--teal-light);
  }
  .contacts li { display: flex; align-items: center; gap: 12px; height: 30px; }
  .contacts svg { width: 20px; height: 20px; flex: none; }
</style>
</head>
<body>

  <section class="card card--front" aria-label="Business card front">
    <div class="front-band"></div>
    <div class="accent-bar"></div>
    <div class="brand">
      <span class="brand__name"><span class="brand__mark"></span>CORVANE MEDIA</span>
      <span class="brand__tagline">Online advertisement agency</span>
    </div>
  </section>

  <section class="card card--back" aria-label="Business card back">
    <div class="brand">
      <span class="brand__name"><span class="brand__mark"></span>CORVANE MEDIA</span>
      <span class="brand__tagline">Online advertisement agency</span>
    </div>
    <div class="accent-bar"></div>
    <div class="back-strip">
      <div class="person">
        <div class="person__name">Your Name</div>
        <div class="person__role">Company Position</div>
      </div>
      <ul class="contacts">
        <li>
          <svg viewBox="0 0 20 20" aria-hidden="true"><circle cx="10" cy="10" r="10" fill="#2f8fa6"/><rect x="5" y="6.5" width="10" height="7" fill="none" stroke="#fff" stroke-width="1.3"/><path d="M5 6.5l5 4 5-4" fill="none" stroke="#fff" stroke-width="1.3"/></svg>
          name@domainname.com
        </li>
        <li>
          <svg viewBox="0 0 20 20" aria-hidden="true"><circle cx="10" cy="10" r="10" fill="#2f8fa6"/><path d="M7 5.5c-.8.4-1.3 1.2-1 2.3.8 2.7 2.7 4.8 5.4 5.9 1 .4 1.9 0 2.4-.8l-1.6-1.5-1.2.7c-1.1-.6-2-1.5-2.5-2.6l.8-1.1z" fill="#fff"/></svg>
          000 000 0000
        </li>
      </ul>
    </div>
  </section>

</body>
</html>
```